Machinery Harbor Corp - Business Card Design

Need a new modern designed business card that is different and stands out to represent my equipment financing company. Machinery Harbor Corp finances all types of equipment and all types of industries. We like to do equipment financing a different way by putting customers first and want our card to represent that different approach to business. I want a card that some remembers when they receive it so it sticks in their mind and makes that wow impression.

Card should have a black background so the logo stands out. It can be horizontial or vertical or a combination of both.

Front of card information is below that shows the information that would go on my card. That is where I want a different look or design to stand out. The front could be split black/orange colour so the logo could pop on black side and information on orange side with different lettering. Just outside the box thinking on the front of the card. Open to any type of design.

Back of card is below which i I like unless you have a different spin to provide or a different idea that would make the card better as I am open to anything that looks great.

Target Market(s)

Machinery Harbor Corp deals with business owners in all industries.

Industry/Entity Type

Business

Contact Information for Business Card

Colors

Designer to choose colors to be used in the design.

Requirements
Must have
• Modern
• Different
• Stand Out
• Makes an Impression

```html
<!DOCTYPE html>
<html lang="en">
<head>
<meta charset="utf-8">
<title>Machinery Harbor Corp – Business Card</title>
<link href="https://fonts.googleapis.com/css2?family=Lato:wght@400;700&display=swap" rel="stylesheet">
<style>
  :root {
    --backdrop: #8a7658;
    --card: #1f2326;
    --orange-top: #ee3b26;
    --orange-bottom: #f7901e;
    --brand: #ef6a22;
    --text-light: #f2f2f2;
    --icon: #1f2326;
  }
  html, body {
    margin: 0;
    padding: 0;
    width: 1189px;
    height: 1200px;
    overflow: hidden;
    background: var(--backdrop);
    font-family: "Lato", sans-serif;
  }
  .card {
    position: absolute;
    top: 233px;
    width: 437px;
    height: 764px;
    background: var(--card);
    overflow: hidden;
    box-shadow: 0 10px 24px rgba(0,0,0,0.35);
  }
  .card--back { left: 121px; border-radius: 0 40px 0 40px; }
  .card--front { left: 624px; border-radius: 40px 0 40px 0; }

  .accent-bar {
    position: absolute;
    width: 37px;
    background: linear-gradient(to bottom, var(--orange-top), var(--orange-bottom));
  }
  .card--back .accent-bar { left: 42px; top: 0; height: 279px; }
  .card--front .accent-bar { left: 24px; top: 486px; height: 278px; }

  .website {
    position: absolute;
    writing-mode: vertical-rl;
    color: var(--text-light);
    font-size: 17px;
    letter-spacing: 3.2px;
    white-space: nowrap;
  }
  .card--back .website { left: 49px; top: 311px; }
  .card--front .website { left: 31px; top: 57px; }

  .brand {
    position: absolute;
    text-align: center;
    color: var(--brand);
    font-weight: 400;
    text-transform: uppercase;
    line-height: 1.25;
  }
  .brand__square {
    display: block;
    margin: 0 auto 14px;
    width: 14px;
    height: 14px;
    background: var(--brand);
  }
  .card--back .brand { left: 180px; width: 230px; top: 620px; font-size: 22px; letter-spacing: 2px; }
  .card--front .brand { left: 90px; width: 260px; top: 240px; font-size: 27px; letter-spacing: 2.5px; }

  .person {
    position: absolute;
    left: 83px;
    top: 482px;
    color: var(--text-light);
  }
  .person__name { font-size: 26px; font-weight: 700; margin: 0; line-height: 1.1; }
  .person__role { font-size: 19px; font-weight: 400; margin: 2px 0 0; letter-spacing: 0.3px; }

  .contact {
    position: absolute;
    left: 83px;
    top: 638px;
    color: var(--text-light);
    font-size: 19.5px;
    line-height: 26px;
    margin: 0;
    padding: 0;
    list-style: none;
  }
  .contact-icons {
    position: absolute;
    left: 33px;
    top: 643px;
  }
  .contact-icons svg { display: block; margin-bottom: 8px; }
</style>
</head>
<body>
  <section class="card card--back" aria-label="Card back">
    <div class="accent-bar"></div>
    <div class="website">www.machineryharborcorp.ca</div>
    <div class="brand">
      <span class="brand__square"></span>
      Machinery Harbor<br>Corp
    </div>
  </section>

  <section class="card card--front" aria-label="Card front">
    <div class="website">www.machineryharborcorp.ca</div>
    <div class="brand">
      <span class="brand__square"></span>
      Machinery Harbor<br>Corp
    </div>

    <div class="accent-bar"></div>

    <div class="person">
      <p class="person__name">DEAN MARLOW</p>
      <p class="person__role">PRESIDENT</p>
    </div>

    <div class="contact-icons" aria-hidden="true">
      <svg width="20" height="16" viewBox="0 0 20 16">
        <path d="M1 6 C1 2 19 2 19 6 L15 7 L14 5 C11 4 9 4 6 5 L5 7 Z" fill="var(--icon)"/>
        <rect x="4" y="8" width="12" height="7" rx="1" fill="var(--icon)"/>
      </svg>
      <svg width="20" height="14" viewBox="0 0 20 14">
        <rect x="1" y="1" width="18" height="12" fill="none" stroke="var(--icon)" stroke-width="1.6"/>
        <path d="M1 1 L10 8 L19 1 M1 13 L8 6.5 M19 13 L12 6.5" fill="none" stroke="var(--icon)" stroke-width="1.4"/>
      </svg>
    </div>

    <ul class="contact">
      <li>403.555.0182</li>
      <li>dean@machineryharborcorp.ca</li>
    </ul>
  </section>
</body>
</html>
```